Linear Villas Andalus listings flyer

Linear Villas Andalus are a specialist estate agency focussed solely on selling modern and contemporary homes.

We need an A4 folded flyer to be designed so that Linear Villas Andalus can leaflet drop all of the modern homes for sale in our area to generate new instructions / listings. We need to engage with owners of those types of homes by posting this marketing material through their letter boxes in the hope that they see our funky and modern design and decide to call us about our services to sell their home, if for sale.

We would like to see sharp lines and a modern design (see our logo for style and colour scheme), with lots of white spaces and using photos which can blend in to the background to provide a powerful and impacting image to set us aside from any other direct mail leaflets which may be in their post box. It needs to show

* Quality
* Style
* Modern and forward thinking in design and outlook
* Professionalism

Front page
Top:
Logo of Linear Villas Andalus.
Helping you sell your modern home. It’s all we do!

4 property photos in a grid position

Bottom banner
If you are thinking of selling, read on…

INSIDE LEFT & RIGHT (DOUBLE PAGE POSSIBLY BLANK WHITE BACKGROUND)
Title: Use Linear Villas Andalus – the specialist modern homes agency to sell your home

We bring an exciting and dynamic mix of modern marketing with good old fashioned service to guarantee only the most qualified clients will be viewing your home (use online marketing image)

Marketing packages include stylish online brochures, professional photography, stunning drone video footage, informative video walk thru’s and unique floor plans (use drone and floor plan images)

Targeted social media campaigns focusing on international clientele actively looking to buy property in southern Spain (use social media image)

Bespoke, powerful advertising packages enable worldwide exposure for both online and traditional channels to market. We can be as discreet or as visible as you want us to be to sell your home

During our 20 years on the Costa del Sol, we have built up an enviable network of collaborating agents meaning you only have to instruct one expert real estate agent, Linear Villas Andalus, to gain maximum exposure for your home

BACK PAGE

If you want service that matches the value of your home, contact us today for a private, personalised consultation. Linear Villas Andalus. It’s all we do.

Suite 14
Corvena Business Centre
Avenida Los Almendros
Corvena, Marbella

Tel: +34 952 618 304
Mobil y Whatsapp: +34 677 482 051
Email: info@linearvillasandalus-example.com
www.linearvillasandalus-example.com

Target Market(s)

Wealthy property owners of contemporary and modern homes who are looking to sell their home

Industry/Entity Type

Real Estate Agent

Font styles to use
Serif
Sans Serif

Colors
606060
e7e7e7
f5f5f5

Requirements
Must have
• Classy, professional, modern design with the ability to stand out from other leaflet drops / direct mail in letter box
Nice to have
• straight lines to border photos
• Maybe extend the lines further than they should so it has the look of an architects plan
• Blend in images to white background in the middle open double page
Should not have
• Lots of different colours

```html
<!DOCTYPE html>
<html lang="en">
<head>
<meta charset="utf-8">
<title>Linear Villas Andalus – Flyer</title>
<link href="https://fonts.googleapis.com/css2?family=Lato:ital,wght@0,300;0,400;0,700;1,300&display=swap" rel="stylesheet">
<style>
:root{
  --ink:#606060;
  --ink-dark:#2e2e30;
  --mist:#e7e7e7;
  --paper:#ffffff;
  --band:#d6d7d9;
  --backdrop:#f5f5f5;
  --text:#333333;
}
*{margin:0;padding:0;box-sizing:border-box}
html,body{width:1200px;height:861px;overflow:hidden;background:var(--backdrop);font-family:'Lato',sans-serif;color:var(--text)}
.flyer{position:absolute;left:52px;top:43px;width:1096px;height:775px;background:var(--paper);box-shadow:0 2px 10px rgba(0,0,0,.18)}
.page{position:absolute;top:0;height:775px;width:548px;overflow:hidden}
.page--back{left:0;background:var(--paper)}
.page--front{left:548px;background:linear-gradient(90deg,#e4e4e4 0,#fff 90px,#fff 100%)}

/* back page */
.plan-photo{position:absolute;left:0;top:0;width:548px;height:450px;background:linear-gradient(135deg,#ffffff 0%,#f1f1f1 55%,#e2e2e2 100%)}
.divider-strip{position:absolute;left:0;top:450px;width:548px;height:13px;background:var(--band)}
.brand{position:absolute;left:0;width:548px;text-align:center;display:flex;justify-content:center;align-items:center;gap:8px}
.brand__mark{width:12px;height:12px;background:var(--ink)}
.brand__name{font-weight:400;font-size:17px;letter-spacing:.5px;color:var(--ink-dark);text-transform:uppercase}
.page--back .brand{top:576px}
.closing{position:absolute;left:40px;top:615px;width:468px;text-align:center;font-size:10.5px;line-height:14px;color:var(--text)}
.rule{position:absolute;left:0;top:670px;width:548px;height:3px;background:var(--ink-dark)}
.address{position:absolute;left:70px;top:694px;font-size:10.5px;line-height:13.6px;font-style:normal}
.contacts{position:absolute;left:264px;top:690px;list-style:none;font-size:10.5px;line-height:13.6px}
.contacts li{display:flex;align-items:center;gap:5px}
.contacts svg{width:10px;height:10px;fill:var(--ink-dark)}

/* front page */
.tagline{position:absolute;left:0;width:548px;text-align:center;color:var(--ink)}
.tagline--lead{top:69px;font-size:21px;font-weight:300}
.tagline--big{top:102px;font-size:64px;font-weight:300;letter-spacing:1px;line-height:1}
.gallery-band{position:absolute;left:0;top:210px;width:548px;height:406px;background:var(--band)}
.photo{position:absolute;border:3px solid #fff;background:linear-gradient(180deg,#3f7fcf 0%,#e9eef2 50%,#7bb86a 100%)}
.photo--a{left:24px;top:25px;width:306px;height:175px}
.photo--b{left:337px;top:25px;width:187px;height:175px}
.photo--c{left:24px;top:206px;width:188px;height:175px}
.photo--d{left:218px;top:206px;width:306px;height:175px;background:linear-gradient(180deg,#2f76c8 0%,#f1f1f1 45%,#44b7e0 100%)}
.page--front .brand{top:680px;left:54px;width:200px;height:90px;background:#fff;justify-content:center}
.page--front .brand__name{font-size:15px}
.teaser{position:absolute;left:352px;top:700px;font-size:17.5px;line-height:22px;font-style:italic;font-weight:300;color:var(--ink-dark)}
</style>
</head>
<body>
<main class="flyer">
  <section class="page page--back">
    <div class="plan-photo" role="img" aria-label="Architectural floor plan drawing of a kitchen and bathroom on white paper"></div>
    <div class="divider-strip"></div>
    <div class="brand"><span class="brand__mark"></span><span class="brand__name">Linear Villas Andalus</span></div>
    <p class="closing">If you want service that matches the value of your home, contact us today for a private, personalised consultation. Linear Villas Andalus. It’s all we do.</p>
    <div class="rule"></div>
    <address class="address">Suite 14,<br>Corvena Business Centre<br>Avenida Los Almendros<br>Corvena, Marbella</address>
    <ul class="contacts">
      <li><svg viewBox="0 0 10 10"><path d="M1 3h8v6H1zM2 1h6v2H2z"/></svg>+34 952 618 304</li>
      <li><svg viewBox="0 0 10 10"><path d="M2 1l2 2-1 1c1 1 2 2 3 3l1-1 2 2-1 2C4 9 1 6 0 2z"/></svg>+34 677 482 051</li>
      <li><svg viewBox="0 0 10 10"><path d="M0 2h10v7H0zM1 3l4 3 4-3v-.5L5 5 1 2.5z" fill-rule="evenodd"/></svg>info@linearvillasandalus-example.com</li>
      <li><svg viewBox="0 0 10 10"><circle cx="5" cy="5" r="4.5"/></svg>www.linearvillasandalus-example.com</li>
    </ul>
  </section>

  <section class="page page--front">
    <p class="tagline tagline--lead">Helping You Sell Your Modern Home.</p>
    <h1 class="tagline tagline--big">IT’S ALL WE DO!</h1>
    <div class="gallery-band">
      <div class="photo photo--a" role="img" aria-label="Terraced white modern villas with lawn and pool"></div>
      <div class="photo photo--b" role="img" aria-label="White modern villa with garden terrace and sun loungers"></div>
      <div class="photo photo--c" role="img" aria-label="Contemporary white house with cypress trees"></div>
      <div class="photo photo--d" role="img" aria-label="Modern villa with large pool and hills behind"></div>
    </div>
    <div class="brand"><span class="brand__mark"></span><span class="brand__name">Linear Villas Andalus</span></div>
    <p class="teaser">If you are thinking<br>of selling, read on...</p>
  </section>
</main>
</body>
</html>
```